Business Card Design

New business card design

Target Market(s)

Residential & Commercial Property Managers

Industry/Entity Type

Plumbing Services

Contact Information for Business Card

Name - Rowan Keddle, title - Director, Phone Number - 0431 286 517, email - rowan@tbk-plumbing.com.au, Company ABN - 73 215 904 386,

Font styles to use
Sans Serif

Colors
0054AA
0677BA
7BADD7
CADEEF
E8F1F8

```html
<!DOCTYPE html>
<html lang="en">
<head>
<meta charset="utf-8">
<title>TBK Plumbing Services – Business Card</title>
<link rel="stylesheet" href="https://fonts.googleapis.com/css2?family=Questrial&family=Roboto+Condensed:wght@300;400&display=swap">
<style>
  :root {
    --ink: #1e232a;
    --aqua: #00adee;
    --paper: #ffffff;
    --stage: #b6b6b6;
    --muted: #7a7a72;
    --text: #33363a;
    --rule: #8a8a8a;
  }
  * { margin: 0; padding: 0; box-sizing: border-box; }
  html, body { width: 1200px; height: 1200px; overflow: hidden; }
  body { background: var(--stage); position: relative; font-family: "Roboto Condensed", sans-serif; }

  .card {
    position: absolute;
    top: 303px;
    height: 594px;
    overflow: hidden;
    box-shadow: 4px 4px 4px rgba(0,0,0,0.55);
  }

  /* Front */
  .card--front { left: 201px; width: 369px; background: var(--ink); }
  .front__band { position: absolute; left: 0; right: 0; top: 352px; bottom: 0; background: var(--aqua); }
  .front__disc {
    position: absolute; left: 0; top: 184px; width: 369px; height: 369px;
    border-radius: 50%; background: var(--paper);
  }
  .wordmark {
    position: absolute; left: 0; right: 0; text-align: center;
    font-family: "Questrial", sans-serif; color: var(--ink); letter-spacing: 2px; line-height: 1;
  }
  .front .wordmark, .card--front .wordmark { top: 262px; font-size: 72px; }
  .tagline {
    position: absolute; left: 0; right: 0; text-align: center;
    font-family: "Roboto Condensed", sans-serif; font-weight: 300;
    color: var(--muted); letter-spacing: 9px; font-size: 11px; text-transform: lowercase;
  }
  .card--front .tagline { top: 366px; }

  /* Back */
  .card--back { left: 599px; width: 364px; background: var(--paper); }
  .card--back .wordmark { top: 78px; font-size: 72px; }
  .card--back .tagline { top: 176px; }

  .contact-frame {
    position: absolute; left: 47px; top: 284px; width: 272px; height: 263px;
    border: 5px solid var(--ink); border-radius: 26px;
    text-align: center;
  }
  .contact__name {
    margin-top: 44px; font-family: "Questrial", sans-serif;
    font-size: 22px; color: var(--ink); letter-spacing: 0.5px; line-height: 1;
  }
  .contact__role { margin-top: 2px; font-size: 17px; color: var(--aqua); line-height: 1.1; }
  .contact__rule { width: 40px; height: 1px; background: var(--rule); margin: 10px auto 0; }
  .contact__line { font-size: 17px; color: var(--text); line-height: 22px; }
  .contact__phone { margin-top: 13px; }
  .contact__rule--second { margin-top: 19px; }
  .contact__abn { margin-top: 15px; }
  .contact__abn-label { color: var(--aqua); }
  .frame-dot {
    position: absolute; left: 171px; top: 552px; width: 22px; height: 22px;
    border-radius: 50%; background: var(--aqua);
  }
</style>
</head>
<body>
  <section class="card card--front" aria-label="Card front">
    <div class="front__band"></div>
    <div class="front__disc"></div>
    <div class="wordmark">tbk</div>
    <div class="tagline">plumbing services</div>
  </section>

  <section class="card card--back" aria-label="Card back">
    <div class="wordmark">tbk</div>
    <div class="tagline">plumbing services</div>
    <div class="contact-frame">
      <p class="contact__name">Rowan Keddle</p>
      <p class="contact__role">Director</p>
      <div class="contact__rule"></div>
      <p class="contact__line contact__phone">0431 286 517</p>
      <p class="contact__line">rowan@tbk-plumbing.com.au</p>
      <div class="contact__rule contact__rule--second"></div>
      <p class="contact__line contact__abn"><span class="contact__abn-label">Company ABN</span> - 73 215 904 386</p>
    </div>
    <div class="frame-dot"></div>
  </section>
</body>
</html>
```